Commercial Waterproofing Modern Business Cards

We are a Commercial Waterproofing company. We do a variety of jobs on the exterior of buildings. We repel from the top or scaffold to reach the areas. Cut out and recaulk expansion joints and apply sealants, brick/concrete repairs, seal window frame perimeters, and much more. Our website is www.tallwallmend.com.
We are looking for a new business card design that would look more modern and cutting edge. We like the transparent paper and had thought about using our logo, but maybe pulling it apart to where the building part is kind of in the background. I have attached 2 different logos that we use regularly. We want the design to be a little funky, but professional at the same time. We really don't want the logo to be incorporated by itself, but you can use the logo and take out the buildings and just use the name or vice versa. Please don't just put the logo on the card and the words around that.

Target Market(s)

Property Managers/Building Maintenance

Industry/Entity Type

Business

Contact Information for Business Card

Dorian Vellstrom President
Office (555)418-2097
Mobile (555)604-7351

Font styles to use
Serif

Requirements
Must have
• Nice overall design, somehow pulling from the logo for the design
Nice to have
• Look artsy and modern with a nice quality paper
Should not have
• Too many words or distracting designs. The logo 'as is'

```html
<!DOCTYPE html>
<html lang="en">
<head>
<meta charset="utf-8">
<title>Tallwall Mend — Business Card</title>
<link href="https://fonts.googleapis.com/css2?family=Montserrat:wght@300;400;500&display=swap" rel="stylesheet">
<style>
  :root {
    --page-bg: #e9ebee;
    --card-blue: #0f4e93;
    --card-blue-deep: #0a3f7c;
    --card-glow: #1a5fa8;
    --cream: #efe3b0;
    --white: #f4f7fb;
    --accent: #2fa4dc;
    --icon-glyph: #e8f6fd;
  }
  * { margin: 0; padding: 0; box-sizing: border-box; }
  html, body {
    width: 1200px;
    height: 800px;
    overflow: hidden;
    background: var(--page-bg);
    font-family: "Montserrat", Arial, sans-serif;
  }
  .card {
    position: absolute;
    left: 100px;
    top: 114px;
    width: 1000px;
    height: 572px;
    border-radius: 34px;
    background: radial-gradient(ellipse at 55% 45%, var(--card-glow) 0%, var(--card-blue) 45%, var(--card-blue-deep) 100%);
    box-shadow: 0 18px 40px rgba(10, 30, 60, 0.25);
    color: var(--white);
  }
  .brand {
    position: absolute;
    left: 70px;
    top: 150px;
    width: 320px;
    display: flex;
    flex-direction: column;
    align-items: center;
    gap: 28px;
  }
  .brand-scene {
    width: 260px;
    height: 150px;
    border-radius: 6px;
    background: linear-gradient(180deg, rgba(239, 227, 176, 0.55), rgba(239, 227, 176, 0.25));
  }
  .brand-name {
    font-weight: 400;
    font-size: 38px;
    letter-spacing: 1px;
    color: var(--cream);
    white-space: nowrap;
  }
  .divider {
    position: absolute;
    left: 455px;
    top: 130px;
    width: 2px;
    height: 300px;
    background: linear-gradient(180deg, rgba(255,255,255,0.9), rgba(255,255,255,0.6) 60%, rgba(255,255,255,0));
  }
  .person {
    position: absolute;
    right: 70px;
    top: 52px;
    text-align: right;
  }
  .person-name {
    font-weight: 500;
    font-size: 34px;
    letter-spacing: 0.5px;
    color: var(--white);
  }
  .person-title {
    font-weight: 300;
    font-size: 28px;
    letter-spacing: 1.5px;
    color: var(--accent);
    margin-top: 2px;
  }
  .contacts {
    position: absolute;
    right: 44px;
    top: 268px;
    list-style: none;
    display: flex;
    flex-direction: column;
    align-items: flex-end;
    gap: 22px;
  }
  .contact {
    display: flex;
    align-items: center;
    gap: 18px;
    font-weight: 300;
    font-size: 30px;
    letter-spacing: 2px;
    color: var(--white);
  }
  .contact-icon { width: 48px; height: 48px; flex: none; }
</style>
</head>
<body>
  <main class="card">
    <section class="brand">
      <div class="brand-scene" role="img" aria-label="Skyline illustration area in cream tones"></div>
      <div class="brand-name">Tallwall Mend</div>
    </section>

    <div class="divider"></div>

    <header class="person">
      <div class="person-name">Dorian Vellstrom</div>
      <div class="person-title">President</div>
    </header>

    <ul class="contacts">
      <li class="contact">
        <span>(555)418-2097</span>
        <svg class="contact-icon" viewBox="0 0 48 48" aria-hidden="true">
          <polygon points="24,2 44,13 44,35 24,46 4,35 4,13" fill="var(--accent)"/>
          <path d="M17 14c2-1 3 0 4 3l1 3c0 1-1 2-2 3 1 3 3 5 6 6 1-1 2-2 3-2l3 1c3 1 4 2 3 4-1 2-3 3-5 3-8-1-14-7-15-15 0-3 1-5 2-6z" fill="var(--icon-glyph)"/>
        </svg>
      </li>
      <li class="contact">
        <span>(555)604-7351</span>
        <svg class="contact-icon" viewBox="0 0 48 48" aria-hidden="true">
          <polygon points="24,2 44,13 44,35 24,46 4,35 4,13" fill="var(--accent)"/>
          <rect x="17" y="11" width="14" height="26" rx="2.5" fill="none" stroke="var(--icon-glyph)" stroke-width="2.5"/>
          <circle cx="24" cy="32.5" r="1.6" fill="var(--icon-glyph)"/>
        </svg>
      </li>
      <li class="contact">
        <span>www.tallwallmend.com</span>
        <svg class="contact-icon" viewBox="0 0 48 48" aria-hidden="true">
          <polygon points="24,2 44,13 44,35 24,46 4,35 4,13" fill="var(--accent)"/>
          <rect x="13" y="14" width="22" height="15" rx="1.5" fill="var(--icon-glyph)"/>
          <rect x="21" y="29" width="6" height="4" fill="var(--icon-glyph)"/>
          <rect x="18" y="33" width="12" height="2" fill="var(--icon-glyph)"/>
        </svg>
      </li>
    </ul>
  </main>
</body>
</html>
```